plumbers buisness card

A buisness card for a plumbing buisness
needs to have a water theme with navy blue, light blue and white
with an image of either a water drop, pipes, tools or something relating to plumbing and incorperating my buisness name as a logo

"Kettering Plumbing" is the words that need to stand out with "& gasfitting" to be smaller

spelling error on brief, "maintenance"
and also could you include my email d_kettering@mailwave.com.au

Industry/Entity Type

Plumbing

Contact Information for Business Card

Kettering Plumbing & Gasfitting

declan kettering
0432961085

specialising in
-new homes
-maitenance
-renovations

license no.
-73840

```html
<!DOCTYPE html>
<html lang="en">
<head>
<meta charset="utf-8">
<title>Kettering Plumbing &amp; Gasfitting – Business Card</title>
<link rel="stylesheet" href="https://fonts.googleapis.com/css2?family=Source+Sans+3:wght@400;600;700&display=swap">
<style>
  :root {
    --backdrop: #b9805d;
    --label: #ffffff;
    --card-top: #ffffff;
    --card-mid: #d9eef9;
    --card-bottom: #7cc4ec;
    --ink: #333333;
    --photo-dark: #4a5666;
    --photo-light: #c3ccd5;
  }
  * { margin: 0; padding: 0; box-sizing: border-box; }
  html, body {
    width: 1200px; height: 424px; overflow: hidden;
    background: var(--backdrop);
    font-family: "Source Sans 3", "Myriad Pro", Arial, sans-serif;
  }
  .sheet { position: relative; width: 1200px; height: 424px; }
  .side-label {
    position: absolute; top: 16px; width: 200px; text-align: center;
    color: var(--label); font-size: 29px; font-weight: 400;
    font-family: Arial, Helvetica, sans-serif;
  }
  .side-label--front { left: 189px; }
  .side-label--back { left: 775px; }
  .card {
    position: absolute; top: 83px; width: 539px; height: 308px; overflow: hidden;
    background: linear-gradient(180deg, var(--card-top) 0%, var(--card-mid) 45%, var(--card-bottom) 100%);
    color: var(--ink);
  }
  .card--front { left: 31px; }
  .card--back { left: 630px; }
  .tap-photo {
    position: absolute; left: 0; top: 0; width: 395px; height: 112px;
    background: linear-gradient(100deg, var(--photo-dark) 0%, #7d8a98 55%, var(--photo-light) 100%);
  }
  .front-text { position: absolute; right: 21px; top: 134px; text-align: right; }
  .brand-name { font-weight: 700; font-size: 27px; line-height: 1; letter-spacing: 0.2px; }
  .brand-sub { font-size: 16px; margin-top: 13px; margin-right: 2px; }
  .contact-name { font-weight: 700; font-size: 13.5px; margin-top: 21px; }
  .details { font-size: 13px; line-height: 18px; margin-top: 23px; }
  .details b { font-weight: 700; }
  .back-text { position: absolute; left: 212px; top: 230px; text-align: center; width: 280px; }
  .back-text .brand-name { font-size: 31px; }
  .back-text .brand-sub { font-size: 18px; margin-top: 4px; margin-left: 14px; }
</style>
</head>
<body>
<div class="sheet">
  <div class="side-label side-label--front">Front</div>
  <div class="side-label side-label--back">Back</div>

  <section class="card card--front">
    <div class="tap-photo" role="img" aria-label="Photo of a chrome tap with a water drop falling from it"></div>
    <div class="front-text">
      <div class="brand-name">Kettering Plumbing</div>
      <div class="brand-sub">&amp; gasfitting</div>
      <div class="contact-name">Declan Kettering &nbsp;:&nbsp; 0432961085</div>
      <div class="details">
        <div><b>Specialising in</b> :&nbsp; new homes &nbsp;- maintenance - renovations</div>
        <div><b>e-mail :</b> d_kettering@mailwave.com.au | license no. -73840</div>
      </div>
    </div>
  </section>

  <section class="card card--back">
    <div class="tap-photo" role="img" aria-label="Photo of a chrome tap with a water drop falling from it"></div>
    <div class="back-text">
      <div class="brand-name">Kettering Plumbing</div>
      <div class="brand-sub">&amp; gasfitting</div>
    </div>
  </section>
</div>
</body>
</html>
```